Looking for a cool & simple business-card-design for digital agency

Hi!

We are a web agency that offers Reputation Management, Vextor & Seo Services and software development. We like cool things, we like innovative styles.

We have uploaded our logo.

Project Deadline Extended Reason: Client does not want any designs with the colorful logo. Please send us submissions ONLY with the blac and white logo. What the client would like to see:1) Back of the card: is a silver logo on a black background2) front of the card with all the data, please use white background and black logo thank you Added Friday, May 8, 2015

Industry/Entity Type

Software

```html
<!DOCTYPE html>
<html lang="de">
<head>
<meta charset="utf-8">
<title>Norvalen AG – Visitenkarte</title>
<link rel="stylesheet" href="https://fonts.googleapis.com/css2?family=Open+Sans:wght@300;400;600;700&display=swap">
<style>
  :root {
    --page: #d9d6d1;
    --card-white: #ffffff;
    --card-edge: #e4e4e4;
    --ink: #1a1a1a;
    --ink-soft: #555555;
    --band: #0b0b0b;
    --band-hi: #2a2a2a;
    --contact: #f2f2f2;
    --silver-hi: #f0f0f0;
    --silver-lo: #8c8c8c;
    --back-hi: #2b2b2b;
    --back-lo: #050505;
  }
  * { box-sizing: border-box; margin: 0; padding: 0; }
  html, body { width: 1200px; height: 1023px; overflow: hidden; }
  body {
    background: var(--page);
    font-family: "Open Sans", Arial, sans-serif;
    position: relative;
  }
  .card {
    position: absolute;
    width: 620px;
    height: 354px;
    border-radius: 22px;
    overflow: hidden;
    box-shadow: 0 10px 28px rgba(0,0,0,0.35);
  }
  .card-front { left: 70px; top: 90px; background: var(--card-white); border: 1px solid var(--card-edge); }
  .card-back {
    left: 510px; top: 570px;
    background: linear-gradient(135deg, var(--back-hi) 0%, var(--back-lo) 55%, #151515 100%);
  }
  .band { position: absolute; inset: 0; }
  .brand { position: absolute; display: flex; align-items: center; gap: 14px; }
  .brand-mark { width: 22px; height: 22px; background: var(--ink); }
  .brand-text { border-left: 1px solid #999; padding-left: 12px; }
  .brand-name { font-weight: 700; font-size: 34px; line-height: 1; color: var(--ink); letter-spacing: 0.5px; }
  .brand-tag { font-weight: 300; font-size: 17px; letter-spacing: 5px; color: var(--ink); margin-top: 4px; }
  .card-front .brand { left: 48px; top: 58px; }
  .person { position: absolute; left: 112px; top: 168px; }
  .person-name { font-weight: 700; font-size: 17px; color: var(--ink); }
  .person-role { font-weight: 400; font-size: 14px; color: var(--ink-soft); margin-top: 2px; }
  .contacts { position: absolute; left: 196px; top: 226px; list-style: none; }
  .contacts li {
    display: flex; align-items: center; gap: 9px;
    color: var(--contact); font-size: 16px; line-height: 27px;
  }
  .contacts svg { width: 14px; height: 14px; flex: none; }
  .card-back .brand { left: 86px; top: 120px; }
  .card-back .brand-mark { background: var(--silver-lo); }
  .card-back .brand-text { border-left-color: #777; }
  .card-back .brand-name, .card-back .brand-tag { color: #c9c9c9; }
  .card-back .brand-name { font-size: 40px; }
  .card-back .brand-tag { font-size: 19px; letter-spacing: 7px; }
  .back-url { position: absolute; left: 96px; top: 220px; color: #bdbdbd; font-size: 13px; }
</style>
</head>
<body>
  <section class="card card-front" aria-label="Vorderseite">
    <svg class="band" viewBox="0 0 620 354" aria-hidden="true">
      <defs>
        <linearGradient id="bandShade" x1="0" y1="0" x2="1" y2="1">
          <stop offset="0" stop-color="var(--band-hi)"/>
          <stop offset="0.5" stop-color="var(--band)"/>
        </linearGradient>
      </defs>
      <polygon points="182,206 620,206 620,354 160,354 160,228" fill="url(#bandShade)"/>
    </svg>

    <div class="brand">
      <span class="brand-mark"></span>
      <div class="brand-text">
        <div class="brand-name">Norvalen AG</div>
        <div class="brand-tag">DIGITALE STRATEGIEN</div>
      </div>
    </div>

    <div class="person">
      <div class="person-name">Mara Feld</div>
      <div class="person-role">Director</div>
    </div>

    <ul class="contacts">
      <li>
        <svg viewBox="0 0 14 14"><path d="M3 1h3l1 3-2 1.5a8 8 0 0 0 3.5 3.5L10 7l3 1v3a2 2 0 0 1-2 2A10 10 0 0 1 1 3a2 2 0 0 1 2-2z" fill="#f2f2f2"/></svg>
        000 555 0142
      </li>
      <li>
        <svg viewBox="0 0 14 14"><rect x="3" y="1" width="8" height="12" rx="1.5" fill="none" stroke="#f2f2f2" stroke-width="1.4"/></svg>
        333 555 0199
      </li>
      <li>
        <svg viewBox="0 0 14 14"><rect x="1" y="3" width="12" height="8" fill="#f2f2f2"/><path d="M1 3l6 5 6-5" fill="none" stroke="#0b0b0b" stroke-width="1.2"/></svg>
        info@norvalenag.com
      </li>
      <li>
        <svg viewBox="0 0 14 14"><circle cx="7" cy="7" r="6" fill="none" stroke="#f2f2f2" stroke-width="1.2"/><ellipse cx="7" cy="7" rx="2.5" ry="6" fill="none" stroke="#f2f2f2" stroke-width="1"/><path d="M1 7h12" stroke="#f2f2f2" stroke-width="1"/></svg>
        www.norvalenag.com
      </li>
    </ul>
  </section>

  <section class="card card-back" aria-label="Rückseite">
    <div class="brand">
      <span class="brand-mark"></span>
      <div class="brand-text">
        <div class="brand-name">Norvalen AG</div>
        <div class="brand-tag">DIGITALE STRATEGIEN</div>
      </div>
    </div>
    <div class="back-url">www.norvalenag.com</div>
  </section>
</body>
</html>
```